eCommerce Website Design for Children's Book Service

I am looking for a 5 page eCommerce website that includes a Shopping Cart. 'Lumiva Books' is the title of the company and its logo is attached. 'Sprouting wonder in words,' is the company's motto and 'spring green' is the main color. The website needs to appeal to families. Images of books and/or maple seeds (helicopter seeds) moving are part of the graphics.
Updates

I have updated my brief and I would like my website design to include 5 pages: home, about, products (books), blog, contact. WordPress is the web format that I am most comfortable with.

Target Market(s)

Families with young children

Coding

Coded - Design and coding required

Number of Pages Required

5+ page

Requirements
Must have
• Shopping cart page; contact page, books page with spaces of photos to go, blog page; spring green color
Nice to have
• A graphic that relates to motto : "sprouting wonder in words"
• WordPress

```html
<!DOCTYPE html>
<html lang="en">
<head>
<meta charset="utf-8">
<title>Lumiva Books — Home</title>
<link href="https://fonts.googleapis.com/css2?family=Lato:ital,wght@0,400;0,700;0,900;1,400&display=swap" rel="stylesheet">
<style>
:root{
  --green:#5cb843;
  --green-dark:#2f8f22;
  --green-deep:#1f7a1a;
  --green-light:#a9d98a;
  --mint:#eef7e6;
  --mint-2:#e2f1d6;
  --ink:#222;
  --grey:#555;
  --white:#fff;
  --star:#f2a100;
  --footer-bar:#e6f2dc;
}
*{box-sizing:border-box;margin:0;padding:0}
html,body{width:1200px;height:3482px;overflow:hidden}
body{position:relative;font-family:'Lato',sans-serif;color:var(--ink);background:var(--white)}
.abs{position:absolute}
a{color:inherit;text-decoration:none}

/* header & hero */
.hero-bg{left:0;top:0;width:1200px;height:700px;background:radial-gradient(ellipse at 30% 40%,#ffffff 0%,#f3f9ee 55%,#e7f3dc 100%)}
.account-links{top:18px;left:832px;font-size:13px;color:var(--ink)}
.account-links span{margin:0 6px}
.brand{left:162px;top:62px;width:170px;text-align:center;color:var(--green-dark);font-weight:400}
.brand-name{font-size:46px;line-height:1}
.brand-sub{font-size:14px;letter-spacing:4px;margin-top:4px}
.brand-dot{left:226px;top:22px;width:40px;height:40px;border-radius:50%;background:var(--green)}
.main-nav{top:72px;left:416px;display:flex;gap:28px;font-size:18px;color:var(--ink)}
.cart{left:986px;top:60px;width:46px;height:46px;border-radius:50%;background:var(--green);display:flex;align-items:center;justify-content:center}
.hero-title{left:155px;top:252px;width:420px;color:var(--green-dark);font-weight:700;font-size:41px;line-height:48px;letter-spacing:-0.3px;white-space:nowrap;z-index:3}
.hero-text{left:157px;top:358px;width:420px;font-size:20px;line-height:27px;color:var(--green-dark)}
.btn{display:flex;align-items:center;justify-content:center;border-radius:30px;background:var(--green);color:var(--white);font-weight:700}
.hero-btn{left:153px;top:436px;width:186px;height:56px;font-size:20px}
.hero-photo{left:590px;top:152px;width:460px;height:460px;border-radius:50%;border:10px solid var(--green);background:radial-gradient(circle at 50% 45%,#e9c9a8 0%,#b98b6a 45%,#6e7c8a 100%);z-index:2}
.dots{top:642px;left:564px;display:flex;gap:12px;z-index:3}
.dots i{width:16px;height:16px;border-radius:50%;border:2px solid #666;display:block}
.dots i.on{background:var(--green-dark);border-color:var(--green-dark)}

/* section titles */
.sec-title{width:1200px;left:0;text-align:center;color:var(--green-dark);font-weight:700;font-size:30px}
.sprout{left:576px;width:48px;height:28px}

/* cards */
.card{border:2px solid #ccc;border-radius:46px;background:var(--white);text-align:center;color:var(--green)}
.card .cover{margin:0 auto;box-shadow:3px 4px 8px rgba(0,0,0,.25)}
.card h3{font-weight:400;font-size:24px;margin-top:16px}
.card p{font-size:16px;line-height:18px;color:var(--grey);margin:10px 24px 0}
.card .price{font-size:26px;font-weight:900;color:var(--green-deep);margin:8px 0 0}
.card.active{background:linear-gradient(#6cc552,#4fae3a);border-color:#4fae3a;color:var(--white)}
.card.active p,.card.active .price{color:var(--white)}
.arrow{width:30px;height:60px}
.buy-btn{background:var(--green-dark);color:var(--white);font-weight:700;border-radius:30px;display:flex;align-items:center;justify-content:center}

.best-bg{left:0;top:1330px;width:1200px;height:680px;background:radial-gradient(ellipse at 50% 40%,#ffffff 0%,#f2f9ec 60%,#e6f2dc 100%)}
.card.small{border-radius:40px}
.card.small h3{font-size:22px;margin-top:10px}
.card.small p{font-size:14px;margin:4px 10px 0}
.card.small .price{font-size:24px;margin-top:4px}

/* about */
.about-bg{left:0;top:1990px;width:1200px;height:580px;background:radial-gradient(ellipse at 60% 40%,#5fc13f 0%,#3a9a22 55%,#237a14 100%)}
.about-photo{left:156px;top:2052px;width:408px;height:408px;border-radius:50%;border:10px solid var(--white);background:radial-gradient(circle at 50% 35%,#f6e6cf 0%,#c99a74 40%,#7a5a55 75%,#4a3a40 100%)}
.about-title{left:598px;top:2100px;color:var(--white);font-weight:700;font-size:32px}
.about-text{left:598px;top:2162px;width:450px;color:var(--white);font-size:16px;line-height:28px}
.about-btn{left:594px;top:2350px;width:172px;height:50px;background:var(--green-light);color:var(--white);font-size:19px}

/* reviews */
.review{width:284px;height:216px;border:2px solid var(--green);border-radius:8px;background:var(--white);text-align:center;padding:52px 26px 0}
.review q{display:block;font-style:italic;color:var(--grey);font-size:14px;line-height:20px;quotes:none}
.review .q{position:absolute;font-size:48px;color:#444;font-family:Georgia,serif;line-height:1}
.review b{display:block;font-size:14px;margin-top:12px}
.stars{color:var(--star);font-size:20px;letter-spacing:2px;margin-top:4px}
.avatar{width:70px;height:70px;border-radius:50%;border:3px solid var(--white);box-shadow:0 0 0 1px #ddd}
.seed{border-radius:50%/60%}

/* footer */
.footer-bg{left:0;top:3040px;width:1200px;height:372px;background:linear-gradient(#e8f4de,#dcefcf)}
.f-col h4{color:var(--green-dark);font-weight:700;font-size:18px;margin-bottom:14px}
.f-col li{list-style:none;font-size:14px;line-height:24px;color:var(--ink)}
.email{left:752px;top:3191px;width:281px;height:47px;border-radius:24px;background:var(--white);display:flex;align-items:center;justify-content:space-between;padding:0 20px;font-size:15px}
.social{width:38px;height:38px;border-radius:50%;background:var(--white);border:1px solid #ccc}
.pay{width:44px;height:24px;border-radius:3px}
.copy-bar{left:0;top:3412px;width:1200px;height:70px;background:var(--footer-bar);display:flex;align-items:center;justify-content:center;font-size:14px;color:var(--grey)}
</style>
</head>
<body>

<!-- Hero -->
<div class="abs hero-bg" role="img" aria-label="Soft pattern of drifting maple seeds on pale green"></div>
<div class="abs account-links"><a href="#">My Account</a><span>|</span><a href="#">Login</a><span>|</span><a href="#">Register</a></div>
<div class="abs brand-dot"></div>
<div class="abs brand"><div class="brand-name">Lumiva</div><div class="brand-sub">BOOKS</div></div>
<nav class="abs main-nav"><a href="#">About Us</a><a href="#">Products</a><a href="#">Our Books</a><a href="#">Blogs</a><a href="#">Shop Now</a><a href="#">Contact</a></nav>
<a class="abs cart" href="#" aria-label="Cart"><svg width="24" height="22" viewBox="0 0 24 22" fill="none" stroke="#fff" stroke-width="2"><path d="M1 2h4l3 12h12l3-9H7"/><circle cx="10" cy="19" r="1.6" fill="#fff"/><circle cx="18" cy="19" r="1.6" fill="#fff"/></svg></a>

<svg class="abs" style="left:0;top:540px" width="1200" height="170" viewBox="0 0 1200 170" preserveAspectRatio="none">
  <path d="M0 80 C300 20 500 140 800 70 S1100 20 1200 50 V170 H0Z" fill="#a9d98a"/>
  <path d="M0 110 C300 50 520 160 820 95 S1100 50 1200 75 V170 H0Z" fill="#4fae3a"/>
  <path d="M0 135 C320 80 540 170 840 120 S1100 80 1200 105 V170 H0Z" fill="#fff"/>
</svg>

<h1 class="abs hero-title">SPROUTING<br>WONDER IN WORDS</h1>
<p class="abs hero-text">Vivamus porttitor purus nisi eleifend libero tempus libero lectus feugiat felis</p>
<a class="abs btn hero-btn" href="#">Shop Now</a>
<div class="abs hero-photo" role="img" aria-label="Photo of a family reading a book together"></div>
<div class="abs dots"><i></i><i class="on"></i><i></i></div>

<!-- New arrivals -->
<svg class="abs sprout" style="top:752px" viewBox="0 0 48 28"><path d="M24 26 C20 16 12 10 2 12 C10 4 20 8 24 20 C28 8 38 4 46 10 C36 10 28 16 24 26Z" fill="#2f8f22"/></svg>
<h2 class="abs sec-title" style="top:788px">NEW ARRIVALS</h2>
<svg class="abs arrow" style="left:106px;top:1003px" viewBox="0 0 30 60"><path d="M26 2 L4 30 L26 58" fill="none" stroke="#999" stroke-width="3"/></svg>
<svg class="abs arrow" style="left:1066px;top:1003px" viewBox="0 0 30 60"><path d="M4 2 L26 30 L4 58" fill="none" stroke="#999" stroke-width="3"/></svg>

<div class="abs card active" style="left:162px;top:847px;width:281px;height:394px;padding-top:28px">
  <div class="cover" style="width:112px;height:176px;background:linear-gradient(#fff 0 30%,#1e6fc2 30% 55%,#eef 55%)" role="img" aria-label="Book cover"></div>
  <h3>Book Title</h3>
  <p>Vivamus porttitor purus nisi eleifend libero a tempus</p>
  <div class="price">$15.99</div>
</div>
<a class="abs buy-btn" href="#" style="left:213px;top:1202px;width:172px;height:50px;font-size:19px">Buy Now</a>

<div class="abs card" style="left:464px;top:847px;width:281px;height:394px;padding-top:30px">
  <div class="cover" style="width:112px;height:180px;background:linear-gradient(160deg,#fff 0 35%,#1aa98a 35% 70%,#0d6e5b 70%)" role="img" aria-label="Book cover"></div>
  <h3>Book Title</h3>
  <p>Vivamus porttitor purus nisi eleifend libero a tempus</p>
  <div class="price">$30.99</div>
</div>
<div class="abs card" style="left:763px;top:847px;width:281px;height:394px;padding-top:30px">
  <div class="cover" style="width:112px;height:180px;background:linear-gradient(#1f7a2a,#0f5a1a)" role="img" aria-label="Book cover"></div>
  <h3>Book Title</h3>
  <p>Vivamus porttitor purus nisi eleifend libero a tempus</p>
  <div class="price">$25.99</div>
</div>

<!-- Best selling -->
<div class="abs best-bg" role="img" aria-label="Soft pattern of drifting maple seeds on pale green"></div>
<svg class="abs" style="left:0;top:1320px" width="1200" height="130" viewBox="0 0 1200 130" preserveAspectRatio="none">
  <rect width="1200" height="20" fill="#fff"/>
  <path d="M0 20 C300 80 700 10 1200 60 V0 H0Z" fill="#fff"/>
  <path d="M0 25 C350 100 750 20 1200 70 V40 C800 0 350 80 0 15Z" fill="#2f8f22"/>
  <path d="M0 15 C350 80 800 0 1200 40 V25 C800 -10 350 65 0 5Z" fill="#a9d98a"/>
</svg>
<svg class="abs sprout" style="top:1444px" viewBox="0 0 48 28"><path d="M24 26 C20 16 12 10 2 12 C10 4 20 8 24 20 C28 8 38 4 46 10 C36 10 28 16 24 26Z" fill="#2f8f22"/></svg>
<h2 class="abs sec-title" style="top:1480px">BEST SELLLING</h2>
<svg class="abs arrow" style="left:96px;top:1676px" viewBox="0 0 30 60"><path d="M26 2 L4 30 L26 58" fill="none" stroke="#444" stroke-width="3"/></svg>
<svg class="abs arrow" style="left:1074px;top:1676px" viewBox="0 0 30 60"><path d="M4 2 L26 30 L4 58" fill="none" stroke="#444" stroke-width="3"/></svg>

<div class="abs card small" style="left:146px;top:1541px;width:214px;height:310px;padding-top:38px">
  <div class="cover" style="width:104px;height:156px;background:linear-gradient(#2a2440 0 20%,#e7577a 20% 60%,#f3c6a0 60%)" role="img" aria-label="Book cover"></div>
  <h3>Book Title</h3><p>Vivamus porttitor purus</p><div class="price">$30.99</div>
</div>
<a class="abs buy-btn" href="#" style="left:186px;top:1644px;width:136px;height:38px;font-size:16px;background:var(--green)">Buy Now</a>
<div class="abs card small" style="left:378px;top:1578px;width:214px;height:310px;padding-top:36px">
  <div class="cover" style="width:104px;height:150px;background:linear-gradient(#222 0 70%,#6fbf2a 70%)" role="img" aria-label="Book cover"></div>
  <h3>Book Title</h3><p>Vivamus porttitor purus</p><div class="price">$30.99</div>
</div>
<div class="abs card small" style="left:610px;top:1541px;width:214px;height:310px;padding-top:44px">
  <div class="cover" style="width:118px;height:150px;background:linear-gradient(#fff 0 40%,#1e7fa0 40% 80%,#fff 80%)" role="img" aria-label="Book cover"></div>
  <h3>Book Title</h3><p>Vivamus porttitor purus</p><div class="price">$30.99</div>
</div>
<div class="abs card small" style="left:842px;top:1578px;width:214px;height:310px;padding-top:36px">
  <div class="cover" style="width:104px;height:150px;background:linear-gradient(#f6d8b0 0 25%,#d2463a 25% 60%,#fff 60%)" role="img" aria-label="Book cover"></div>
  <h3>Book Title</h3><p>Vivamus porttitor purus</p><div class="price">$30.99</div>
</div>

<!-- About -->
<div class="abs about-bg" role="img" aria-label="Close-up of a green leaf"></div>
<svg class="abs" style="left:0;top:1960px" width="1200" height="90" viewBox="0 0 1200 90" preserveAspectRatio="none">
  <path d="M0 0 H1200 V20 C900 60 600 20 300 50 C180 62 80 50 0 40Z" fill="#eaf4e1"/>
  <path d="M0 40 C80 50 180 62 300 50 C600 20 900 60 1200 20 V32 C900 70 600 32 300 62 C180 74 80 62 0 52Z" fill="#a9d98a"/>
</svg>
<div class="abs about-photo" role="img" aria-label="Illustration of a child flying on an open book"></div>
<h2 class="abs about-title">ABOUT US</h2>
<p class="abs about-text">Pellentesque faucibus Ut accumsan ultricies elit Maecenas at justo id velit placerat molestie Donec dictum lectus non odio Cras a ante vitae enim iaculis aliquam<br>Mauris nunc quam venenatis nec euismod sit amet egestas placerat est Pellentesque habitant morbi tristique senectus et netus et malesuada fames ac turpis egestas</p>
<a class="abs btn about-btn" href="#">Learn More</a>
<svg class="abs" style="left:0;top:2480px" width="1200" height="110" viewBox="0 0 1200 110" preserveAspectRatio="none">
  <path d="M0 60 C300 90 700 110 1200 20 V110 H0Z" fill="#a9d98a"/>
  <path d="M0 75 C300 100 700 115 1200 40 V110 H0Z" fill="#fff"/>
</svg>

<!-- Reviews -->
<div class="abs seed" style="left:30px;top:2700px;width:140px;height:200px;background:radial-gradient(#d8eeb0,#9fcf6a);transform:rotate(-30deg);opacity:.8" role="img" aria-label="Maple seed"></div>
<div class="abs seed" style="left:1040px;top:2600px;width:130px;height:190px;background:radial-gradient(#e2f2c0,#a6d470);transform:rotate(20deg);opacity:.8" role="img" aria-label="Maple seed"></div>
<h2 class="abs sec-title" style="top:2592px">REVIEWS</h2>

<div class="abs review" style="left:165px;top:2692px">
  <span class="q" style="left:22px;top:26px">“</span><q>Morbi diam mauris viverra in gravida eu mattis in ante Morbi eget arcu Morbi porta libero id ullamcorper nonummy</q><span class="q" style="right:22px;top:112px">”</span>
  <b>By Author Name</b><div class="stars">★★★★★</div>
</div>
<div class="abs review" style="left:466px;top:2692px">
  <span class="q" style="left:22px;top:26px">“</span><q>Morbi diam mauris viverra in gravida eu mattis in ante Morbi eget arcu Morbi porta libero id ullamcorper nonummy</q><span class="q" style="right:22px;top:112px">”</span>
  <b>By Author Name</b><div class="stars">★★★★</div>
</div>
<div class="abs review" style="left:766px;top:2692px">
  <span class="q" style="left:22px;top:26px">“</span><q>Morbi diam mauris viverra in gravida eu mattis in ante Morbi eget arcu Morbi porta libero id ullamcorper nonummy</q><span class="q" style="right:22px;top:112px">”</span>
  <b>By Author Name</b><div class="stars">★★★★★</div>
</div>
<div class="abs avatar" style="left:272px;top:2656px;background:linear-gradient(#cfcfcf,#8a8f96)" role="img" aria-label="Reviewer portrait"></div>
<div class="abs avatar" style="left:573px;top:2656px;background:linear-gradient(#e9d3b8,#c9a27a)" role="img" aria-label="Reviewer portrait"></div>
<div class="abs avatar" style="left:873px;top:2656px;background:linear-gradient(#d9c2b0,#3a2a28)" role="img" aria-label="Reviewer portrait"></div>

<!-- Footer -->
<div class="abs footer-bg"></div>
<svg class="abs" style="left:0;top:2950px" width="1200" height="130" viewBox="0 0 1200 130" preserveAspectRatio="none">
  <path d="M0 60 C250 100 500 60 800 40 S1100 10 1200 0 V130 H0Z" fill="#a9d98a"/>
  <path d="M0 85 C250 120 520 80 820 62 S1100 35 1200 28 V130 H0Z" fill="#4fae3a"/>
  <path d="M0 100 C260 130 540 100 840 85 S1100 60 1200 55 V130 H0Z" fill="#fff"/>
  <path d="M0 115 C260 135 560 115 860 105 S1100 85 1200 80 V130 H0Z" fill="#e8f4de"/>
</svg>
<div class="abs brand-dot" style="left:226px;top:3116px"></div>
<div class="abs brand" style="top:3166px"><div class="brand-name">Lumiva</div><div class="brand-sub">BOOKS</div></div>

<div class="abs f-col" style="left:395px;top:3146px"><h4>QUICK LINKS</h4><ul><li>About Us</li><li>Our Products</li><li>Books</li><li>Shop Now</li><li>Contact</li></ul></div>
<div class="abs f-col" style="left:573px;top:3146px"><h4>RESOURCES</h4><ul><li>My Account</li><li>Cart</li><li>Wishlist</li><li>Support</li><li>Register</li></ul></div>
<div class="abs f-col" style="left:757px;top:3146px"><h4>NEWSLETTER SIGN UP</h4></div>
<div class="abs email"><span>Email address</span><svg width="22" height="16" viewBox="0 0 22 16" fill="none" stroke="#333" stroke-width="2"><path d="M1 8h19M13 1l7 7-7 7"/></svg></div>
<div class="abs social" style="left:754px;top:3256px" aria-label="Social link"></div>
<div class="abs social" style="left:805px;top:3256px" aria-label="Social link"></div>
<div class="abs social" style="left:856px;top:3256px" aria-label="Social link"></div>
<div class="abs social" style="left:907px;top:3256px" aria-label="Social link"></div>
<div class="abs pay" style="left:758px;top:3314px;background:#c7d3e6" aria-label="Payment method"></div>
<div class="abs pay" style="left:808px;top:3314px;background:#b8d0e6" aria-label="Payment method"></div>
<div class="abs pay" style="left:858px;top:3314px;background:#e8d0b8" aria-label="Payment method"></div>
<div class="abs pay" style="left:908px;top:3314px;background:#d4dcea" aria-label="Payment method"></div>

<div class="abs copy-bar">© 2019 Company Name&nbsp; All right reserved</div>

</body>
</html>
```